Social Media Graphics - Oakline Push REVISED

Create 6-7 individual social media graphics (square size) to encourage folks to join our online course called:

The Harvest Ledger Circle
How to Launch a Multi-Million Business From Scratch
Sign Up Today!

IMPORTANT: Make the largest and most prominent text on the graphic be: How to Launch a Multi-Million Business From Scratch

For the color scheme of the graphics, let's try a blue color palette; make sure the graphics appeal to both men and women

Make sure each graphic contains 1 of the 3 pics attached (crop pic as needed); and make sure one of the graphics is all TEXT only.

Target Market(s)

men and women looking to start a business

Industry/Entity Type

Entrepreneurship

Colors
0054AA
0677BA
7BADD7
CADEEF
E8F1F8

Requirements
Must have
• All the text and use the 3 pics provided; one graphic can be all text; Simple, modern design that's easy to read

```html
<!DOCTYPE html>
<html lang="en">
<head>
<meta charset="UTF-8">
<title>The Harvest Ledger Circle – Social Graphic</title>
<link href="https://fonts.googleapis.com/css2?family=Bungee&family=Poppins:wght@600;700&display=swap" rel="stylesheet">
<style>
  :root {
    --blue-deep: #0054AA;
    --blue-mid: #0677BA;
    --blue-soft: #7BADD7;
    --blue-pale: #CADEEF;
    --blue-mist: #E8F1F8;
    --white: #FFFFFF;
    --bg-dark: #0b4f8f;
  }
  * { margin: 0; padding: 0; box-sizing: border-box; }
  html, body { width: 1200px; height: 1200px; overflow: hidden; }
  body { background: var(--white); }
  .graphic {
    position: relative;
    width: 1200px;
    height: 1200px;
    overflow: hidden;
    background:
      radial-gradient(ellipse at 20% 10%, #1a6fb8 0%, transparent 55%),
      radial-gradient(ellipse at 80% 30%, #2a7fc4 0%, transparent 50%),
      linear-gradient(160deg, #1465ac 0%, var(--bg-dark) 60%, #0a4a86 100%);
  }
  .headline {
    position: absolute;
    left: 88px;
    top: 78px;
    width: 800px;
    font-family: "Bungee", sans-serif;
    font-size: 84px;
    line-height: 108px;
    color: var(--white);
    text-transform: uppercase;
    letter-spacing: 1px;
  }
  .program-name {
    position: absolute;
    left: 88px;
    top: 680px;
    width: 430px;
    font-family: "Poppins", sans-serif;
    font-weight: 700;
    font-size: 52px;
    line-height: 62px;
    color: var(--white);
  }
  .cta-button {
    position: absolute;
    left: 76px;
    top: 918px;
    width: 357px;
    height: 71px;
    border-radius: 36px;
    background: var(--blue-mist);
    display: flex;
    align-items: center;
    justify-content: center;
    font-family: "Poppins", sans-serif;
    font-weight: 700;
    font-size: 25px;
    color: var(--blue-deep);
    text-transform: uppercase;
  }
  .hosts-frame {
    position: absolute;
    left: 0;
    top: 0;
    width: 1200px;
    height: 1200px;
  }
</style>
</head>
<body>
  <main class="graphic">
    <h1 class="headline">How to launch a multi-million business from scratch</h1>
    <p class="program-name">The Harvest Ledger Circle</p>
    <div class="cta-button">Sign up today!</div>

    <svg class="hosts-frame" viewBox="0 0 1200 1200" xmlns="http://www.w3.org/2000/svg">
      <defs>
        <linearGradient id="hostsPhotoTone" x1="0" y1="0" x2="1" y2="1">
          <stop offset="0" stop-color="#e9e3da"/>
          <stop offset="0.5" stop-color="#b9a592"/>
          <stop offset="1" stop-color="#6f6a68"/>
        </linearGradient>
      </defs>
      <circle cx="1255" cy="1255" r="790" fill="var(--blue-mid)"/>
      <circle cx="1255" cy="1255" r="768" fill="url(#hostsPhotoTone)" role="img" aria-label="Photo of the two course hosts, a woman in a blue blazer and a man in a grey suit holding a microphone, smiling on stage"/>
    </svg>
  </main>
</body>
</html>
```